Corvane Business Cards

Front of business card will have logo, name, address, & telephone number. Back of card will have a list of services provided - Roads, Substation Pads, Temporary Pads, Site Pads, Land Leveling, Powerline Row Cleaning, Land Clearing, Gates, Fencing, Construction Entrances, Excavation, Trenching, Underground Utilities, Directional Boring, Pile Driving. We are a construction company that uses heavy equipment like bulldozers, motor graders/blades, dump trucks, backhoes, hydro axes, & skid loaders. We build roads, pads, & install electric utility lines & waterlines underground. This logo is new. The word "Construction" can be smaller as uploaded 2 example edited logos. We will be using this card design for many employees.
Target Market(s)
Industrial Electric Powerline, Wind Turbine, Solar Panel, & Water Utility companies.
Contact Information for Business Card
Name/Position - Dwayne Halster - Owner
Address: 4875 FM 309
Merkel, TX 79412
Phone number - (325) 482-5096

```html
<!DOCTYPE html>
<html lang="en">
<head>
<meta charset="utf-8">
<title>Corvane Construction Business Cards</title>
<link href="https://fonts.googleapis.com/css2?family=Poppins:wght@400;500;600&display=swap" rel="stylesheet">
<style>
  :root {
    --maroon: #3a0c18;
    --ink: #2b0a12;
    --text-grey: #555555;
    --band-grey: #9b9b9b;
    --card-white: #f7f7f7;
    --backdrop: #e9e6e2;
    --white: #ffffff;
  }
  * { box-sizing: border-box; margin: 0; padding: 0; }
  html, body {
    width: 1125px; height: 1200px; overflow: hidden;
    background: var(--backdrop);
    font-family: "Poppins", sans-serif;
  }
  .canvas { position: relative; width: 1125px; height: 1200px; }

  .card {
    position: absolute; left: 150px; width: 825px; height: 470px;
    box-shadow: 0 4px 10px rgba(0,0,0,0.25);
  }

  /* Front */
  .card-front { top: 98px; background: var(--card-white); overflow: hidden; }
  .front-brand {
    position: absolute; left: 60px; top: 0; width: 285px; height: 100%;
    display: flex; flex-direction: column; justify-content: center; align-items: center;
    color: var(--maroon); font-weight: 600; text-align: center;
  }
  .front-brand .brand-name { font-size: 58px; line-height: 1; letter-spacing: 1px; }
  .front-brand .brand-sub { font-size: 25px; line-height: 1.3; letter-spacing: 1px; margin-top: 12px; }
  .divider {
    position: absolute; left: 393px; top: 140px; width: 2px; height: 192px;
    background: var(--maroon);
  }
  .contact { position: absolute; left: 435px; top: 138px; color: var(--text-grey); }
  .contact .person { font-size: 25px; font-weight: 600; color: var(--ink); line-height: 1.1; letter-spacing: 0.5px; }
  .contact .role { font-size: 18px; color: #222; margin-bottom: 16px; }
  .contact .address { font-size: 18.5px; line-height: 1.3; margin-bottom: 16px; }
  .contact .line { display: flex; align-items: center; gap: 9px; font-size: 18.5px; line-height: 1.25; }
  .contact .line svg { width: 14px; height: 14px; fill: var(--ink); flex: none; }
  .front-band {
    position: absolute; left: 0; bottom: 0; width: 100%; height: 15px;
  }

  /* Back */
  .card-back {
    top: 630px; background: var(--maroon); color: var(--white);
  }
  .back-brand {
    position: absolute; left: 0; right: 0; top: 150px; text-align: center;
    font-weight: 600; font-size: 96px; line-height: 1; letter-spacing: 2px;
  }
  .back-brand .brand-sub { display: block; font-size: 30px; letter-spacing: 4px; margin-top: 14px; }
  .services {
    position: absolute; left: 0; right: 0; bottom: 34px; text-align: center;
    font-size: 18.5px; line-height: 1.2;
  }
</style>
</head>
<body>
<div class="canvas">

  <section class="card card-front">
    <div class="front-brand">
      <div class="brand-name">CORVANE</div>
      <div class="brand-sub">CONSTRUCTION</div>
    </div>
    <div class="divider"></div>
    <div class="contact">
      <div class="person">DWAYNE HALSTER</div>
      <div class="role">Owner</div>
      <div class="address">4875 FM 309<br>Dunmore, TX 79412</div>
      <div class="line">
        <svg viewBox="0 0 24 24" aria-hidden="true"><path d="M6.6 10.8a15.1 15.1 0 0 0 6.6 6.6l2.2-2.2c.3-.3.7-.4 1-.2 1.1.4 2.3.6 3.6.6.6 0 1 .4 1 1V20c0 .6-.4 1-1 1A17 17 0 0 1 3 4c0-.6.4-1 1-1h3.5c.6 0 1 .4 1 1 0 1.2.2 2.4.6 3.6.1.3 0 .7-.2 1z"/></svg>
        <span>(325) 482-5096</span>
      </div>
      <div class="line">
        <svg viewBox="0 0 24 24" aria-hidden="true"><path d="M2 5h20v14H2z" fill="var(--ink)"/><path d="M3 6l9 7 9-7" fill="none" stroke="#f7f7f7" stroke-width="1.6"/></svg>
        <span>info@corvaneconstruction.com</span>
      </div>
      <div class="line">
        <svg viewBox="0 0 24 24" aria-hidden="true"><circle cx="12" cy="12" r="10"/><path d="M2 12h20M12 2c3 3 3 17 0 20M12 2c-3 3-3 17 0 20" fill="none" stroke="#f7f7f7" stroke-width="1.4"/></svg>
        <span>www.corvaneconstruction.com</span>
      </div>
    </div>
    <svg class="front-band" viewBox="0 0 825 15" preserveAspectRatio="none" aria-hidden="true">
      <polygon points="0,0 538,0 532,15 0,15" fill="var(--maroon)"/>
      <polygon points="542,0 825,0 825,15 536,15" fill="var(--band-grey)"/>
    </svg>
  </section>

  <section class="card card-back">
    <div class="back-brand">CORVANE<span class="brand-sub">CONSTRUCTION</span></div>
    <div class="services">
      Roads • Substation Pads • Temporary Pads • Site Pads • Land Leveling<br>
      Powerline Row Cleaning • Land Clearing • Gates • Fencing • Construction Entrances<br>
      Excavation • Trenching • Underground Utilities • Directional Boring • Pile Driving
    </div>
  </section>

</div>
</body>
</html>
```